Social Media App Needs PPT Template

We need a PowerPoint template for a new social media company based in the DC area called "Bold Ledger." We provide an interactive digital platform for executives to share actionable advice. We would like to see designs that use our orange logo color as an accent, but are mainly grey, white, and black. The final design should communicate clean, chic, modern, and professional.

Target Market(s)

Executives

Industry/Entity Type

Information Technology

Font styles to use
Sans Serif

Colors
f78f20
fbe7d2
ffffff
000000
e8e8e8
757575

Requirements
Must have
• My project must have title page and many options for the body of the ppt (graphs, tables, etc). It also needs to be easy to modify. I must have someone who is experienced in creating powerpoint templates.
Nice to have
• It would be nice to have a very modern and clean design that includes the logo on every page, but still leaves a lot of room for the content of the slide
Should not have
• My design project should not look to busy.

```html
<!DOCTYPE html>
<html lang="en">
<head>
<meta charset="utf-8">
<title>Bold Ledger – Chart Slide</title>
<link rel="stylesheet" href="https://fonts.googleapis.com/css2?family=Bebas+Neue&family=Lato:wght@400;700&display=swap">
<style>
  :root {
    --backdrop: #555555;
    --paper: #ffffff;
    --navy: #222c3b;
    --orange: #f3911f;
    --series-grey: #a4a5a8;
    --text: #555555;
    --grid: #b5b5b5;
    --rule: #666666;
  }
  * { margin: 0; padding: 0; box-sizing: border-box; }
  html, body {
    width: 1200px; height: 960px; overflow: hidden;
    background: var(--backdrop);
  }
  .slide {
    position: absolute; left: 0; top: 30px;
    width: 1200px; height: 900px;
    background: var(--paper);
    font-family: "Lato", sans-serif;
    color: var(--text);
  }
  .accent-band {
    position: absolute; left: 0; top: 17px;
    width: 100%; height: 15px;
    background: var(--orange);
  }
  .header-bar {
    position: absolute; left: 0; top: 35px;
    width: 100%; height: 116px;
    background: var(--navy);
  }
  .slide-title {
    position: absolute; left: 51px; top: 25px;
    font-family: "Bebas Neue", sans-serif;
    font-weight: 400; font-size: 72px; line-height: 72px;
    color: var(--paper); letter-spacing: -0.5px;
  }
  .brand {
    position: absolute; right: 46px; top: 40px;
    display: flex; align-items: center; gap: 12px;
  }
  .brand-dot {
    width: 30px; height: 30px; border-radius: 50%;
    background: var(--orange);
  }
  .brand-name {
    font-family: "Lato", sans-serif; font-weight: 700;
    font-size: 30px; letter-spacing: 2px;
    color: var(--paper); text-transform: uppercase;
  }
  .chart {
    position: absolute; left: 0; top: 0;
    width: 1200px; height: 600px;
  }
  .chart text { font-family: "Lato", sans-serif; fill: var(--text); }
  .body-copy {
    position: absolute; left: 61px; top: 628px;
    width: 1085px;
    font-size: 20.5px; line-height: 30.2px;
    text-align: justify;
  }
  .footer-rule {
    position: absolute; left: 806px; top: 830px;
    width: 348px; height: 1.5px; background: var(--rule);
  }
  .footer-note {
    position: absolute; right: 43px; top: 852px;
    font-size: 16.5px; color: var(--text);
  }
</style>
</head>
<body>
<main class="slide">
  <div class="accent-band"></div>
  <header class="header-bar">
    <h1 class="slide-title">Title Goes Here</h1>
    <div class="brand">
      <span class="brand-dot"></span>
      <span class="brand-name">Bold Ledger</span>
    </div>
  </header>

  <svg class="chart" viewBox="0 0 1200 600" aria-label="Area chart of three series across three categories">
    <g class="grid" stroke="var(--grid)" stroke-width="1.2" stroke-dasharray="9 7">
      <line x1="88" y1="225.5" x2="1010" y2="225.5"/>
      <line x1="88" y1="284.2" x2="1010" y2="284.2"/>
      <line x1="88" y1="342.9" x2="1010" y2="342.9"/>
      <line x1="88" y1="401.6" x2="1010" y2="401.6"/>
      <line x1="88" y1="460.3" x2="1010" y2="460.3"/>
    </g>
    <polygon class="series-3" fill="var(--navy)" points="443.4,305.3 1010.3,248 1010.3,519 443.4,519"/>
    <polygon class="series-2" fill="var(--orange)" points="88.5,419 318,302.4 895.6,363.7 1010.3,377 1010.3,519 88.5,519"/>
    <polygon class="series-1" fill="var(--series-grey)" points="88.5,419 438.6,354 720.6,394.8 895.6,363.7 1010.3,342.3 1010.3,519 88.5,519"/>
    <line x1="88.5" y1="225" x2="88.5" y2="519" stroke="#8a8a8a" stroke-width="1.2"/>
    <line x1="82" y1="519" x2="1010" y2="519" stroke="#8a8a8a" stroke-width="1.2"/>
    <g class="value-axis" font-size="21" text-anchor="end">
      <text x="69" y="233">5</text>
      <text x="69" y="292">4</text>
      <text x="69" y="350">3</text>
      <text x="69" y="409">2</text>
      <text x="69" y="468">1</text>
      <text x="69" y="527">0</text>
    </g>
    <g class="category-axis" font-size="21">
      <text x="87.5" y="560">Category 1</text>
      <text x="473.5" y="560">Category 2</text>
      <text x="882" y="560">Category 3</text>
    </g>
    <g class="legend" font-size="21">
      <rect x="1049" y="220" width="12" height="12" fill="var(--series-grey)"/>
      <text x="1066" y="232">Series 1</text>
      <rect x="1049" y="251" width="12" height="12" fill="var(--orange)"/>
      <text x="1066" y="263">Series 2</text>
      <rect x="1049" y="284" width="12" height="12" fill="var(--navy)"/>
      <text x="1066" y="296">Series 3</text>
    </g>
  </svg>

  <p class="body-copy">Duis autem vel eum iriure dolor in hendrerit in vulputate velit esse molestie consequat, vel illum dolore eu feugiat nulla facilisis at vero eros et accumsan et iusto odio dignissim qui blandit praesent luptatum zzril delenit augue duis dolore te feugait nulla facilisi. Nam liber tempor cum soluta nobis eleifend option congue nihil imperdiet doming id quod mazim placerat facer possim assum.</p>

  <div class="footer-rule"></div>
  <p class="footer-note">www.boldledger.com &nbsp;|&nbsp; Page 5</p>
</main>
</body>
</html>
```